"The Plumewright" nails, eyelash extensions and hair extensions. Need an eye catching design for bu

Need an eye catching design focusing on eyelash extensions, nail extensions and hair extensions. I like the colour green, black, glitter, pink?! need the design to be innovative and 'POP'. I'd like more emphasis on lashes and nails.
I'd like the business name and my phone number on the front of card.
Would really like something different and unique.
"The Plumewright"
Nails, Eyelash & Hair Extensions
Mira
0471526093

Target Market(s)

20-40

Industry/Entity Type

Beauty Salon

Contact Information for Business Card

Id like my business name, My name and phone number on the front of card
"The Plumewright".
Mira.
0471526093.
Id like some catchy design involving long lashes with possibly glitter, long hair and nails. Id like the lashes to be the first thing you see at first glance. I'm open to your creative flair. Just need the business card design to 'POP'! I like the colours green, black, pink, silver or gold glitter. wether it's pop art, 3d drawn pictures, isolated pics of lash, nails or hair, card design could be in black and white with isolated colours added..i'm open to your creative flair. use a font which stands out and easy to read.
(The back of the card will be used for writing appointment times.)

Font styles to use
Serif

Colors
6b449b
e667a6
25b39d

Requirements
Must have
• Long lashes, hair, nails.
• one sided
Nice to have
• bright catchy colours, innovative, uniqueness

```html
<!DOCTYPE html>
<html lang="en">
<head>
<meta charset="utf-8">
<title>The Plumewright — Business Cards</title>
<link rel="stylesheet" href="https://fonts.googleapis.com/css2?family=Open+Sans:wght@400;600&display=swap">
<style>
  :root {
    --pink: #e466a6;
    --purple: #6b449b;
    --white: #ffffff;
    --ink: #1b1b1b;
    --backdrop: #ece9e7;
  }
  * { box-sizing: border-box; margin: 0; padding: 0; }
  html, body {
    width: 1200px;
    height: 900px;
    overflow: hidden;
    background: var(--backdrop);
    font-family: "Open Sans", Arial, sans-serif;
  }
  .canvas {
    position: relative;
    width: 1200px;
    height: 900px;
  }
  .card {
    position: absolute;
    border-radius: 14px;
    overflow: hidden;
    box-shadow: 0 6px 18px rgba(0, 0, 0, 0.12);
  }
  .card--front {
    left: 78px;
    top: 34px;
    width: 588px;
    height: 364px;
    background: var(--white);
  }
  .card--back {
    left: 389px;
    top: 506px;
    width: 566px;
    height: 350px;
    background: var(--pink);
  }
  .band {
    position: absolute;
    left: 0;
    width: 100%;
  }
  .card--front .band {
    top: 30px;
    height: 98px;
    background: var(--pink);
  }
  .card--back .band {
    top: 87px;
    height: 97px;
    background: var(--white);
  }
  .emblem-circle {
    position: absolute;
    border-radius: 50%;
  }
  .card--front .emblem-circle {
    left: 228px;
    top: 12px;
    width: 132px;
    height: 132px;
    background: var(--white);
  }
  .card--back .emblem-circle {
    left: 226px;
    top: 62px;
    width: 146px;
    height: 146px;
    background: var(--pink);
  }
  .business-name {
    position: absolute;
    left: 0;
    width: 100%;
    text-align: center;
    font-weight: 400;
    letter-spacing: 0.5px;
  }
  .card--front .business-name {
    top: 158px;
    font-size: 38px;
    color: var(--purple);
  }
  .card--back .business-name {
    top: 212px;
    font-size: 38px;
    color: var(--white);
  }
  .contact {
    position: absolute;
    left: 0;
    top: 258px;
    width: 100%;
    text-align: center;
  }
  .contact__name {
    font-size: 24px;
    font-weight: 600;
    color: var(--pink);
    line-height: 1.3;
  }
  .contact__phone {
    display: inline-flex;
    align-items: center;
    gap: 5px;
    margin-top: 2px;
    font-size: 20px;
    color: var(--ink);
  }
  .contact__phone svg {
    width: 16px;
    height: 16px;
    fill: var(--pink);
  }
</style>
</head>
<body>
<main class="canvas">

  <section class="card card--front" aria-label="Card front">
    <div class="band"></div>
    <div class="emblem-circle"></div>
    <h1 class="business-name">The Plumewright</h1>
    <div class="contact">
      <p class="contact__name">Mira</p>
      <p class="contact__phone">
        <svg viewBox="0 0 24 24" aria-hidden="true">
          <path d="M6.6 10.8c1.4 2.8 3.8 5.1 6.6 6.6l2.2-2.2c.3-.3.7-.4 1-.2 1.1.4 2.3.6 3.6.6.6 0 1 .4 1 1V20c0 .6-.4 1-1 1C10.6 21 3 13.4 3 4c0-.6.4-1 1-1h3.5c.6 0 1 .4 1 1 0 1.3.2 2.5.6 3.6.1.3 0 .7-.2 1l-2.3 2.2z"/>
        </svg>
        0471526093
      </p>
    </div>
  </section>

  <section class="card card--back" aria-label="Card back">
    <div class="band"></div>
    <div class="emblem-circle"></div>
    <h2 class="business-name">The Plumewright</h2>
  </section>

</main>
</body>
</html>
```